Clear Plastic Card Design

I am looking to have a business card designed from my logo icon. I am looking to match the style of a different business card I have attached in the files.
Looking for a card that is plastic, with layers of transparency in the shape of my logo icon (also attached in the files) - not a circle like the other card. The winning design will incorporate the red icon logo on the front and back and include the charity's name, "Light for the Weary Souls" in the same or similar font, as well as an email and phone number. For now, use the email: email@lightfortheweary-mail.org and the phone number 555-382-7194.
We like how the sample business card has transparency, partial and full opacity layers and a matching color scheme. Files will need to be in vector so that our business card printing company can work with it.
UPDATE:
We've some excellent designs in, thank you everyone! I got an early review from the owner, and he requested a minor redirect to find his perfect design. He wants the design to stand out by NOT being a rectangle. Try instead a circle, square, or best yet - something that falls in the outline of the logo icon, either fully or partially. Thank you, everyone!
Light for the Weary Souls text should be incorporated as well as a phone and email.

```html
<!DOCTYPE html>
<html lang="en">
<head>
<meta charset="UTF-8">
<title>Light for the Weary Souls – Round Cards</title>
<link rel="stylesheet" href="https://fonts.googleapis.com/css2?family=Quicksand:wght@500&family=Oswald:wght@500&family=Roboto:wght@900&display=swap">
<style>
  :root {
    --canvas: #efebe7;
    --red-deep: #a80a17;
    --red: #c8101e;
    --red-bright: #e3231b;
    --white: #ffffff;
    --ink: #111111;
    --dash-grey: #6d6d6d;
  }
  * { margin: 0; padding: 0; box-sizing: border-box; }
  html, body { width: 1200px; height: 800px; overflow: hidden; }
  body { background: var(--canvas); position: relative; font-family: "Quicksand", sans-serif; }

  .card { position: absolute; width: 476px; height: 476px; top: 242px; }
  .card--front { left: 110px; }
  .card--back { left: 614px; }
  .card__shape { position: absolute; inset: 0; }

  .front-name {
    position: absolute; left: 0; right: 0; top: 178px;
    text-align: center; color: var(--white);
    font-family: "Quicksand", sans-serif; font-weight: 500;
    font-size: 44px; line-height: 1.15;
  }

  .back-name {
    position: absolute; left: 0; right: 0; top: 72px;
    text-align: center; color: var(--red-bright);
    font-family: "Quicksand", sans-serif; font-weight: 500;
    font-size: 30px; line-height: 1.15;
  }

  .contact { position: absolute; left: 0; right: 0; display: flex; justify-content: center; align-items: center; gap: 8px;
    font-family: "Oswald", sans-serif; font-weight: 500; color: var(--ink); }
  .contact--phone { top: 208px; font-size: 31px; letter-spacing: 0.5px; }
  .contact--email { top: 260px; font-size: 21px; letter-spacing: 0.3px; }
  .contact__icon { width: 26px; height: 26px; flex: none; }
  .contact--email .contact__icon { width: 24px; height: 24px; }
  .email-domain { color: var(--red-bright); }

  .back-title {
    position: absolute; left: 0; right: 0; top: 314px;
    text-align: center; color: var(--red-bright);
    font-family: "Roboto", sans-serif; font-weight: 900;
    font-size: 32px; line-height: 1.15;
  }
</style>
</head>
<body>

  <section class="card card--front">
    <svg class="card__shape" viewBox="0 0 476 476" aria-hidden="true">
      <defs>
        <radialGradient id="frontFill" cx="45%" cy="40%" r="65%">
          <stop offset="0" stop-color="#c8101e"/>
          <stop offset="1" stop-color="#a80a17"/>
        </radialGradient>
      </defs>
      <circle cx="238" cy="238" r="238" fill="url(#frontFill)"/>
      <circle cx="238" cy="238" r="228" fill="none" stroke="#ffffff" stroke-width="2" stroke-dasharray="7 5"/>
    </svg>
    <p class="front-name">Light for the<br>Weary Souls</p>
  </section>

  <section class="card card--back">
    <svg class="card__shape" viewBox="0 0 476 476" aria-hidden="true">
      <defs>
        <clipPath id="backClip"><circle cx="238" cy="238" r="238"/></clipPath>
      </defs>
      <circle cx="238" cy="238" r="238" fill="#ffffff"/>
      <g clip-path="url(#backClip)">
        <ellipse cx="238" cy="500" rx="72" ry="60" fill="#e3231b"/>
      </g>
      <circle cx="238" cy="238" r="228" fill="none" stroke="#6d6d6d" stroke-width="2.5" stroke-dasharray="8 5"/>
    </svg>

    <p class="back-name">Light for the<br>Weary Souls</p>

    <p class="contact contact--phone">
      <svg class="contact__icon" viewBox="0 0 24 24" aria-hidden="true">
        <path fill="#e3231b" d="M2 8c0-2 4-4 10-4s10 2 10 4v2h-5V8.5c-1.5-.6-3.2-.9-5-.9s-3.5.3-5 .9V10H2V8zm4 3h12l2 9H4l2-9zm6 2.2a3 3 0 1 0 0 6 3 3 0 0 0 0-6z"/>
      </svg>
      555-382-7194
    </p>

    <p class="contact contact--email">
      <svg class="contact__icon" viewBox="0 0 24 24" aria-hidden="true">
        <path fill="#e3231b" d="M22 3L2 11l6 2.5L19 6l-9 9v6l3.5-4.5L18 19z"/>
      </svg>
      <span>EMAIL@<span class="email-domain">LIGHTFORTHEWEARY-MAIL</span>.ORG</span>
    </p>

    <h1 class="back-title">LIGHT FOR THE<br>WEARY SOULS</h1>
  </section>

</body>
</html>
```